Business Card Design Project

We are not a new company, but renamed to "Vantorin Kitchens" last year. We specialize in modern high-end cabinetry imports. We would like to communicate a sense of quality and cutting edge technology. Ideally the design would incorporate our logo colors, silver, red and preferably a black, matte background. Though we are open to suggestions.
Logo is attached.
Edit: I have attached rough drafts of the previous cards, this way you will have all necessary content that needs to go on the cards.
Updates
Project Deadline Extended
Reason: We have received a lot of great designs, but due to the sheer number we couldn't respond to all. We will extend the deadline for another 7 days to finalize and provide feedback to designers.
Thank you for your hard work!
Industry/Entity Type
Business
Look and feel
Each slider illustrates characteristics of the customer's brand and the style your logo design should communicate.

```html
<!DOCTYPE html>
<html lang="en">
<head>
<meta charset="utf-8">
<title>Vantorin Kitchens – Business Cards</title>
<link rel="stylesheet" href="https://fonts.googleapis.com/css2?family=Arimo:wght@400;700&display=swap">
<style>
  :root {
    --page-bg: #e7e3de;
    --label: #2a2520;
    --card-dark: #141414;
    --card-mid: #2c2c2c;
    --silver: #c8c8c8;
    --silver-light: #e4e4e4;
    --white: #ffffff;
    --red: #e8202a;
    --band-grey: #c4c4c4;
    --band-text: #222222;
  }
  * { margin: 0; padding: 0; box-sizing: border-box; }
  html, body { width: 1200px; height: 788px; overflow: hidden; }
  body {
    position: relative;
    background: var(--page-bg);
    font-family: "Arimo", Arial, sans-serif;
  }
  .sheet-label {
    position: absolute;
    width: 300px;
    text-align: center;
    font-size: 22px;
    color: var(--label);
  }
  .card {
    position: absolute;
    width: 524px;
    height: 300px;
    border-radius: 22px;
    overflow: hidden;
    background: radial-gradient(ellipse at 50% 40%, var(--card-mid) 0%, var(--card-dark) 75%);
    color: var(--white);
  }
  .card--black { background: #050505; }
  .wordmark {
    position: absolute;
    left: 0; right: 0;
    display: flex;
    justify-content: center;
    align-items: center;
    gap: 12px;
  }
  .wordmark__square {
    width: 18px; height: 18px;
    background: var(--red);
  }
  .wordmark__name {
    font-weight: 700;
    font-size: 27px;
    letter-spacing: 3px;
    text-transform: uppercase;
    color: var(--silver);
  }
  .card--back .wordmark__name { font-size: 31px; }
  .card--back .wordmark__square { width: 21px; height: 21px; }
  .person {
    position: absolute;
    top: 196px;
    left: 0; right: 0;
    text-align: center;
    font-size: 17px;
  }
  .person__name { font-weight: 700; }
  .person--plain .person__name { font-weight: 400; }
  .person__role { font-size: 15px; }
  .contact-line {
    position: absolute;
    top: 231px;
    left: 0; right: 0;
    text-align: center;
    font-size: 13.5px;
  }
  .contact-line b { font-weight: 700; }
  .info-band {
    position: absolute;
    left: 0; bottom: 0;
    width: 524px; height: 32px;
  }
  .info-band__text {
    position: absolute;
    bottom: 8px;
    font-size: 13.5px;
  }
  .info-band__address { left: 26px; color: var(--white); }
  .info-band__email { right: 18px; color: var(--band-text); }
  .texture {
    position: absolute;
  }
  .texture--top {
    left: 0; top: 0; width: 290px; height: 90px;
    background: radial-gradient(ellipse at 50% 30%, #4a4a4a 0%, #202020 45%, transparent 75%);
  }
  .texture--bottom {
    right: 0; bottom: 0; width: 260px; height: 95px;
    background: radial-gradient(ellipse at 45% 60%, #4a4a4a 0%, #202020 45%, transparent 75%);
  }
</style>
</head>
<body>

  <div class="sheet-label" style="left:157px;top:22px;">front</div>
  <div class="sheet-label" style="left:738px;top:22px;">front-1</div>
  <div class="sheet-label" style="left:164px;top:405px;">back</div>
  <div class="sheet-label" style="left:738px;top:405px;">Back - 1</div>

  <!-- Front: president -->
  <section class="card card--front" style="left:55px;top:75px;">
    <div class="wordmark" style="top:107px;">
      <span class="wordmark__square"></span>
      <span class="wordmark__name">Vantorin Kitchens</span>
    </div>
    <p class="person"><span class="person__name">MAREK DOLAN,</span> <span class="person__role">President</span></p>
    <p class="contact-line"><b>p</b> : 555.210.0400 &nbsp;|&nbsp; <b>c</b> : 555.210.0411 &nbsp;|&nbsp; <b>f</b> : 555.210.0433</p>
    <svg class="info-band" viewBox="0 0 524 32" aria-hidden="true">
      <polygon points="0,0 285,0 305,32 0,32" fill="var(--red)"/>
      <polygon points="285,0 300,0 320,32 305,32" fill="#0c0c0c"/>
      <polygon points="300,0 524,0 524,32 320,32" fill="var(--band-grey)"/>
    </svg>
    <span class="info-band__text info-band__address">1820 - 64 Ave., Northfield, AB T0X 1A0</span>
    <span class="info-band__text info-band__email">marek@vantorinkitchens.ca</span>
  </section>

  <!-- Front: director -->
  <section class="card card--front" style="left:623px;top:75px;">
    <div class="wordmark" style="top:107px;">
      <span class="wordmark__square"></span>
      <span class="wordmark__name">Vantorin Kitchens</span>
    </div>
    <p class="person person--plain"><span class="person__name">TOMAS DOLAN,</span> <span class="person__role">Director</span></p>
    <p class="contact-line"><b>p</b> : 555.210.0400 &nbsp;|&nbsp; <b>c</b> : 555.210.0422 &nbsp;|&nbsp; <b>f</b> : 555.210.0433</p>
    <svg class="info-band" viewBox="0 0 524 32" aria-hidden="true">
      <polygon points="0,0 285,0 305,32 0,32" fill="var(--red)"/>
      <polygon points="285,0 300,0 320,32 305,32" fill="#0c0c0c"/>
      <polygon points="300,0 524,0 524,32 320,32" fill="var(--band-grey)"/>
    </svg>
    <span class="info-band__text info-band__address">1820 - 64 Ave., Northfield, AB T0X 1A0</span>
    <span class="info-band__text info-band__email">tomas@vantorinkitchens.ca</span>
  </section>

  <!-- Back -->
  <section class="card card--back" style="left:57px;top:447px;">
    <div class="wordmark" style="top:132px;">
      <span class="wordmark__square"></span>
      <span class="wordmark__name">Vantorin Kitchens</span>
    </div>
  </section>

  <!-- Back - 1 -->
  <section class="card card--back card--black" style="left:625px;top:447px;">
    <div class="texture texture--top" role="img" aria-label="Perforated metal dot texture"></div>
    <div class="texture texture--bottom" role="img" aria-label="Perforated metal dot texture"></div>
    <div class="wordmark" style="top:132px;">
      <span class="wordmark__square"></span>
      <span class="wordmark__name">Vantorin Kitchens</span>
    </div>
  </section>

</body>
</html>
```